Create a wordpress website for Tovarin business solution

This project is to create a complete website with all pages.

Overview
The purpose of this project is to create a full complete website with all pages (16 pages). The site should be professional and modern. The site is for an IT recruiting and IT training company. The site needs to be easy to administer and update content. It should be simple to add pages, videos and testimonials later. I will leave the site layout, color schemes and flow to the designers.

Navigation Menu (Home, who we are, what we do, what makes us different, why it matters, candidate portal, contact us, Blog)

WHO WE ARE should be a drop down menu with link to pages (about us, mission, vision and purpose, our team)

WHAT WE DO should be drop down menu with link to the following pages (IT Recruiting, IT Training, Hardware and software sales)

What makes us different should be single page with different paragraph titles. (We live what we do, we don't compromise quality, we share knowledge, staffing guarantee)

Why it matters should be single page with paragraph titles. (Quickly fill positions, candidate career development)

Candidate portal should links to my portal login page. I can add the correct URL later. I just need it to link to somewhere. I can change it.

Contact us should have (address, phone number, google map and a form to submit request for a call back)

Blog - This link should launch a wordpress blogging module

Target Market(s)

IT RECRUITING AND CONSULTING

Industry/Entity Type

It Company

Coding

Coded - Design and coding required

Requirements
Must have
• Company Logo
• Navigation Menu (Home, who we are, what we do, what makes us different, why it matters, candidate portal, contact us)
• WHO WE ARE should be a drop down menu with link to pages (about us, mission, vision and purpose, our team)
• WHAT WE DO should be drop down menu with link to the following pages (IT Recruiting, IT Training, Hardware and software sales)
• What makes us different should be single page with different paragraph titles. (We live what we do, we don't compromise quality, we share knowledge, staffing guarantee)
• Why it matters should be single page with paragraph titles. (Quickly fill positions, candidate career development)
• Candidate portal should links to my portal login page. I can add the correct URL later. I just need it to link to somewhere. I can change it.
• Contact us should have (address, phone number, google map and a form to submit request for a call back)

```html
<!DOCTYPE html>
<html lang="en">
<head>
<meta charset="utf-8">
<title>Tovarin Business Solution LLC</title>
<link rel="stylesheet" href="https://fonts.googleapis.com/css2?family=Play:wght@400;700&family=Arimo:wght@400;700&display=swap">
<style>
:root{
  --blue:#0b5aa5;
  --blue-deep:#084a8a;
  --orange:#e8731a;
  --orange-dark:#b9560e;
  --ink:#2b2b2b;
  --grey:#7a7a7a;
  --white:#ffffff;
  --dark:#1d1f22;
}
*{box-sizing:border-box;margin:0;padding:0}
html,body{width:1200px;height:3666px;overflow:hidden;background:var(--white)}
body{position:relative;font-family:"Arimo",Arial,sans-serif;color:var(--ink)}
.section{position:absolute;left:0;width:1200px}
.center{position:absolute;left:0;width:1200px;text-align:center}
.heading{font-family:"Play",sans-serif;font-weight:400;text-transform:uppercase;letter-spacing:1px}
.blue{color:var(--blue)}
.orange{color:var(--orange)}
.btn{position:absolute;background:var(--orange);color:var(--white);font-family:"Arimo",sans-serif;font-size:21px;text-transform:uppercase;display:flex;align-items:center;justify-content:center;border-bottom:4px solid var(--orange-dark)}

/* hero */
.hero{top:0;height:680px;overflow:hidden}
.hero-photo{position:absolute;inset:0;background:linear-gradient(180deg,#9fb0be 0%,#6d7f90 28%,#27323e 60%,#1b222b 100%)}
.brand-name{top:210px;font-family:"Arimo",sans-serif;font-weight:700;font-size:60px;line-height:70px;color:var(--blue)}
.hero-text{top:340px;left:150px;width:900px;color:var(--white);font-size:15px;line-height:26px}
.search{position:absolute;top:406px;left:367px;width:466px;height:51px;background:var(--white);display:flex}
.search-field{flex:1;padding:0 18px;display:flex;align-items:center;font-size:16px;color:#555}
.search-btn{width:51px;background:var(--orange);display:flex;align-items:center;justify-content:center}
.play{position:absolute;left:557px;top:474px}

/* nav */
.nav{top:680px;height:60px;background:var(--blue);display:flex;padding-left:78px}
.nav a{color:var(--white);text-decoration:none;font-size:16px;text-transform:uppercase;display:flex;align-items:center;padding:0 17px}
.nav a.active{background:var(--orange);padding:0 18px}

/* welcome */
.welcome{top:740px;height:409px}
.welcome h1{top:52px;font-size:44px;line-height:52px}
.welcome .sub{top:116px;font-size:15px;color:#555}
.welcome .body{top:150px;left:140px;width:920px;font-size:13.5px;line-height:23px;color:var(--grey)}

/* services */
.services{top:1149px;height:716px;overflow:hidden}
.services-photo{position:absolute;inset:0;background:linear-gradient(135deg,#3a3733 0%,#24221f 50%,#403a33 100%)}
.services h2{top:38px;font-size:40px}
.services .sub{top:100px;font-size:15px;color:var(--white)}
.services .body{top:148px;left:170px;width:860px;font-size:14px;line-height:26px;color:#cfcfcf}
.card{position:absolute;top:227px;width:345px;height:430px;background:rgba(0,0,0,.45)}
.card-photo{position:absolute;left:16px;top:10px;width:313px;height:208px;border-radius:6px}
.card h3{position:absolute;top:240px;width:100%;text-align:center;font-size:18px;font-weight:400;color:var(--orange);text-transform:uppercase}
.card p{position:absolute;top:270px;left:30px;width:285px;text-align:center;font-size:13.5px;line-height:25px;color:#e2e2e2}
.card .btn{top:366px;left:90px;width:166px;height:56px}

/* differences */
.split{top:1865px;height:313px;display:flex}
.split-col{width:600px;height:313px;padding:46px 0 0 78px;color:var(--white)}
.split-col.left{background:var(--blue)}
.split-col.right{background:var(--orange);padding-left:28px}
.split-col h2{font-size:32px;margin-bottom:24px}
.split-col p{font-size:14px;line-height:24px;width:500px;margin-bottom:12px}
.split-col li{list-style:none;font-size:14px;line-height:27px;display:flex;align-items:center}
.split-col li::before{content:"";width:14px;height:2px;background:var(--white);margin-right:14px}

/* testimonials */
.testimonials{top:2178px;height:437px}
.testimonials h2{top:42px;font-size:44px}
.testimonials .sub{top:100px;font-size:15px;color:#555}
.quote{position:absolute;left:572px;top:160px}
.testimonials .body{top:232px;left:140px;width:920px;font-size:14px;line-height:26px;color:#555}
.testimonials .site{top:300px;font-size:14px;color:var(--orange)}
.testimonials .client{top:320px;font-family:"Play",sans-serif;font-size:19px;color:var(--blue)}
.dots{position:absolute;top:358px;left:568px;display:flex;gap:18px}
.dots span{width:15px;height:15px;border-radius:50%;background:var(--orange)}
.dots span.on{background:var(--blue)}

/* portal */
.portal{top:2615px;height:365px;overflow:hidden}
.portal-photo{position:absolute;inset:0;background:linear-gradient(90deg,#2a2c2f 0%,#3b3835 50%,#4a3e37 100%)}
.portal h2{top:54px;font-size:44px}
.portal .body{top:122px;font-size:14px;color:#cfcfcf}
.field{position:absolute;top:171px;height:51px;background:rgba(0,0,0,.55);color:var(--white);font-size:14px;display:flex;align-items:center;padding-left:18px}
.portal .btn{top:242px;left:516px;width:166px;height:51px}

/* contact */
.contact{top:2980px;height:623px;overflow:hidden}
.contact-photo{position:absolute;inset:0;background:linear-gradient(180deg,#0d5aa6 0%,#0b4f92 60%,#0a4a88 100%)}
.contact h2{top:40px;font-size:44px;color:var(--white)}
.contact .body{top:128px;left:180px;width:840px;font-size:14px;line-height:28px;color:var(--white)}
.map{position:absolute;left:76px;top:200px;width:401px;height:137px;background:linear-gradient(135deg,#e9e4d8,#d6dccf)}
.info{position:absolute;left:76px;top:364px;color:var(--white);font-size:14px}
.info-row{display:flex;align-items:flex-start;gap:16px;margin-bottom:12px}
.info-row .t{line-height:28px}
.company{color:var(--orange);font-size:18px}
.social{display:flex;gap:10px;margin-top:18px}
.social span{width:42px;height:42px;border-radius:50%;border:2px solid var(--white)}
.social span.fill{background:var(--orange);border-color:var(--orange)}
.form{position:absolute;left:518px;top:200px;width:604px}
.form-field{height:60px;border-bottom:1px solid rgba(255,255,255,.35);padding-top:8px;font-size:14px;color:var(--orange)}
.form-field.area{height:100px;color:var(--white)}
.contact .btn{top:503px;left:518px;width:166px;height:56px;border-bottom-color:var(--white)}

/* footer */
.footer{top:3603px;height:63px;background:var(--orange);display:flex;align-items:center;justify-content:center;color:var(--white);font-size:14px}
.footer b{color:var(--blue);margin-right:4px}
</style>
</head>
<body>

<header class="section hero">
  <div class="hero-photo" role="img" aria-label="Business people in silhouette around a meeting table with a world map backdrop"></div>
  <div class="center brand-name">Tovarin Business Solution LLC</div>
  <p class="center hero-text">Lorem Ipsum is simply dummy text of the printing and typesetting industry. Lorem Ipsum has been the industry's standard dummy text ever since the 1500s, when an unknown printer took a galley of type and scrambled.</p>
  <div class="search">
    <div class="search-field">Search....</div>
    <div class="search-btn">
      <svg width="24" height="24" viewBox="0 0 24 24"><circle cx="10" cy="10" r="7" fill="none" stroke="#fff" stroke-width="3"/><line x1="15" y1="15" x2="22" y2="22" stroke="#fff" stroke-width="3"/></svg>
    </div>
  </div>
  <svg class="play" width="88" height="88" viewBox="0 0 88 88"><circle cx="44" cy="44" r="40" fill="rgba(0,0,0,.3)" stroke="#e8731a" stroke-width="5"/><polygon points="35,26 63,44 35,62" fill="#e8731a"/></svg>
</header>

<nav class="section nav">
  <a class="active">Home</a>
  <a>Who We Are</a>
  <a>What We Do</a>
  <a>What Makes Us Different</a>
  <a>Why It Matters</a>
  <a>Candidate Portal</a>
  <a>Contact Us</a>
</nav>

<section class="section welcome">
  <h1 class="center heading"><span class="blue">Welcome to</span> <span class="orange">Tovarin</span></h1>
  <p class="center sub">Business Solution LLC</p>
  <p class="center body">Lorem Ipsum is simply dummy text of the printing and typesetting industry. Lorem Ipsum has been the industry's standard dummy text ever since the 1500s, when an unknown printer took a galley of type and scrambled it to make a type specimen book.<br>It has survived not only five centuries, but also the leap into electronic typesetting, remaining essentially unchanged. It was popularised in the 1960s with the release of Letraset sheets containing Lorem Ipsum passages, and more recently with desktop publishing software like Aldus PageMaker including versions of Lorem Ipsum.</p>
  <div class="btn" style="top:290px;left:516px;width:166px;height:59px">Know More</div>
</section>

<section class="section services">
  <div class="services-photo" role="img" aria-label="Team working together at laptops in an office"></div>
  <h2 class="center heading"><span class="blue">What</span> <span class="orange">We Do</span></h2>
  <p class="center sub">Our Best Services</p>
  <p class="center body">Lorem Ipsum is simply dummy text of the printing and typesetting industry Lorem Ipsum has been the industry's standard dummy text ever since the 1500s, when an unknown printer took a galley of type and scrambled it to</p>

  <article class="card" style="left:72px">
    <div class="card-photo" role="img" aria-label="Business people shaking hands at a recruiting meeting" style="background:linear-gradient(135deg,#e9edf1,#b8c2cc)"></div>
    <h3>IT Recruiting</h3>
    <p>Lorem Ipsum is simply dummy text of the printing and typesetting industry Lorem Ipsum has been the industry's .</p>
    <div class="btn">Know More</div>
  </article>
  <article class="card" style="left:429px">
    <div class="card-photo" role="img" aria-label="Group of trainees gathered around a computer" style="background:linear-gradient(135deg,#d9c7b3,#8d7766)"></div>
    <h3>IT Training</h3>
    <p>Lorem Ipsum is simply dummy text of the printing and typesetting industry Lorem Ipsum has been the industry's.</p>
    <div class="btn">Know More</div>
  </article>
  <article class="card" style="left:783px">
    <div class="card-photo" role="img" aria-label="Hands typing on a keyboard" style="background:linear-gradient(135deg,#c7d3e0,#5d6f86)"></div>
    <h3>Hardware &amp; Software Sales</h3>
    <p>Lorem Ipsum is simply dummy text of the printing and typesetting industry Lorem Ipsum has been the industry's .</p>
    <div class="btn">Know More</div>
  </article>
</section>

<section class="section split">
  <div class="split-col left">
    <h2 class="heading">What Makes <span class="orange">Us Different</span></h2>
    <p>Lorem Ipsum is simply dummy text of the printing and typesetting industry. Lorem Ipsum has been the industry's standard.</p>
    <ul>
      <li>What We Do ?</li>
      <li>We don't Compromise Quality</li>
      <li>We Share Knowledge</li>
      <li>Staffing Guarantee</li>
    </ul>
  </div>
  <div class="split-col right">
    <h2 class="heading"><span class="blue">Why It</span> Matters</h2>
    <p>Lorem Ipsum is simply dummy text of the printing and typesetting industry. Lorem Ipsum has been the industry's standard.</p>
    <ul>
      <li>Quickly Fill Positions</li>
      <li>Candidate Career Development</li>
    </ul>
  </div>
</section>

<section class="section testimonials">
  <h2 class="center heading blue">Testimonials</h2>
  <p class="center sub">What They About Us</p>
  <svg class="quote" width="56" height="46" viewBox="0 0 56 46"><path d="M4 46V26C4 12 10 4 24 0v8c-7 3-10 8-10 14h10v24zM32 46V26C32 12 38 4 52 0v8c-7 3-10 8-10 14h10v24z" fill="#e8731a"/></svg>
  <p class="center body">Lorem Ipsum is simply dummy text of the printing and typesetting industry. Lorem Ipsum has been the industry's standard dummy text ever since the 1500s, when an unknown printer took a galley of type and scrambled it to make"</p>
  <p class="center site">clientsite.com</p>
  <p class="center client">- Client Name Abcd</p>
  <div class="dots"><span class="on"></span><span></span><span></span><span></span></div>
</section>

<section class="section portal">
  <div class="portal-photo" role="img" aria-label="Candidate working on a laptop"></div>
  <h2 class="center heading"><span class="blue">Candidate</span> <span class="orange">Portal</span></h2>
  <p class="center body">Lorem Ipsum is simply dummy text of the printing and typesetting industry Lorem Ipsum has been</p>
  <div class="field" style="left:237px;width:354px">User Name *</div>
  <div class="field" style="left:601px;width:359px">Password *</div>
  <div class="btn">Login</div>
</section>

<section class="section contact">
  <div class="contact-photo" role="img" aria-label="Person at a desk with a laptop, tinted blue"></div>
  <h2 class="center heading">Contact <span class="orange">Us</span></h2>
  <p class="center body">Lorem Ipsum is simply dummy text of the printing and typesetting industry. Lorem Ipsum has been the industry's standard dummy text ever since the 1500s, when an unknown printer took a galley.</p>
  <div class="map" role="img" aria-label="Street map showing the office location"></div>
  <div class="info">
    <div class="info-row">
      <svg width="26" height="30" viewBox="0 0 26 30"><path d="M13 2a10 10 0 0 0-10 10c0 8 10 16 10 16s10-8 10-16A10 10 0 0 0 13 2z" fill="none" stroke="#e8731a" stroke-width="2"/><circle cx="13" cy="12" r="3.5" fill="none" stroke="#e8731a" stroke-width="2"/></svg>
      <div class="t"><span class="company">TOVARIN Business Solution LLC</span><br>101- Lorem ipsum is simple<br>dummy text of print.</div>
    </div>
    <div class="info-row">
      <svg width="26" height="26" viewBox="0 0 26 26"><path d="M6 3l5 5-3 3c1.5 3 4 5.5 7 7l3-3 5 5-3 4C11 23 3 15 2 6z" fill="#e8731a"/></svg>
      <div class="t">+123 456 7890</div>
    </div>
    <div class="info-row">
      <svg width="26" height="26" viewBox="0 0 26 26"><rect x="2" y="5" width="22" height="16" fill="none" stroke="#e8731a" stroke-width="2"/><path d="M2 5l11 9 11-9" fill="none" stroke="#e8731a" stroke-width="2"/></svg>
      <div class="t">info@tovarin.com</div>
    </div>
    <div class="social"><span class="fill"></span><span></span><span></span></div>
  </div>
  <div class="form">
    <div class="form-field">Your Name</div>
    <div class="form-field">Your Phone</div>
    <div class="form-field">Your E-Mail</div>
    <div class="form-field area">Comments and Questions:</div>
  </div>
  <div class="btn">Login</div>
</section>

<footer class="section footer"><b>&copy;Tovarin Business Solution LLC</b> - 2016. All Rights Reserved</footer>

</body>
</html>
```